Brell Stone Company Business Cards

Front and Back Business Card - logo and text setup - cool design. I need workable photoshop or illustrator files so I can setup each employee card with design that is created
Updates

Hi everyone, thank you for the great entries. Please no more white and blue cards - there are so many already - black and silver only now please. thanks!

Target Market(s)

Construction Industry - Facility Managers

Industry/Entity Type

Construction

Contact Information for Business Card

I really like contemporary simplistic looks - clean neat....not opposed to seeing some black backrounds

Requirements
Must have
• Logo/website address with design on front only - www.brellstone-example.com (logo attached)
• Back:
• Name/Title/Company Address/Phone/email address
Nice to have
• Cool design
Should not have
• Nothing gimmicky like Fire or Water - since we are a Fire Protection company - it has all been done

```html
<!DOCTYPE html>
<html lang="en">
<head>
<meta charset="utf-8">
<title>Brell Stone Company – Business Cards</title>
<link rel="stylesheet" href="https://fonts.googleapis.com/css2?family=PT+Sans:wght@400;700&display=swap">
<style>
  :root {
    --backdrop: #c8cbcf;
    --card-black: #000000;
    --brand-blue: #0524a0;
    --accent-red: #ff2222;
    --text-white: #ffffff;
    --divider: #555555;
    --font-main: "PT Sans", sans-serif;
  }
  * { margin: 0; padding: 0; box-sizing: border-box; }
  html, body {
    width: 1200px;
    height: 1193px;
    overflow: hidden;
    background: var(--backdrop);
    font-family: var(--font-main);
  }
  .card {
    position: absolute;
    width: 873px;
    height: 499px;
    border-radius: 42px;
    overflow: hidden;
    background: var(--card-black);
    color: var(--text-white);
  }
  .card--front { left: 61px; top: 71px; }
  .card--back  { left: 258px; top: 627px; }

  .front-waves { position: absolute; inset: 0; width: 100%; height: 100%; }

  .holder {
    position: absolute;
    right: 54px;
    top: 44px;
    text-align: right;
  }
  .holder__name { font-size: 34px; font-weight: 700; line-height: 1.1; }
  .holder__title { font-size: 28px; font-weight: 400; line-height: 1.25; }

  .company-name {
    font-weight: 700;
    color: var(--brand-blue);
    white-space: nowrap;
    line-height: 1;
  }
  .card--front .company-name {
    position: absolute;
    left: 51px;
    top: 205px;
    font-size: 46px;
  }

  .contact-list {
    position: absolute;
    left: 48px;
    top: 350px;
    list-style: none;
  }
  .contact-list li {
    display: flex;
    align-items: center;
    gap: 10px;
    font-size: 20px;
    height: 38px;
    white-space: nowrap;
  }
  .contact-list svg { width: 22px; height: 22px; flex: none; }

  .divider {
    position: absolute;
    left: 378px;
    top: 394px;
    width: 1px;
    height: 58px;
    background: var(--divider);
  }
  .address {
    position: absolute;
    left: 404px;
    top: 392px;
    font-size: 20px;
    line-height: 33px;
    font-style: normal;
    white-space: nowrap;
  }

  .card--back .company-name {
    position: absolute;
    left: 0;
    right: 0;
    top: 200px;
    text-align: center;
    font-size: 64px;
  }
  .back-url {
    position: absolute;
    left: 0;
    right: 0;
    top: 440px;
    text-align: center;
    font-size: 22px;
    letter-spacing: 0.25em;
  }
</style>
</head>
<body>

<section class="card card--front" aria-label="Business card front">
  <svg class="front-waves" viewBox="0 0 1050 600" preserveAspectRatio="none" aria-hidden="true">
    <rect width="1050" height="600" fill="var(--brand-blue)"/>
    <path d="M0,100 C40,38 120,32 200,32 C460,32 700,170 1050,296 L1050,600 L0,600 Z" fill="var(--card-black)"/>
    <path d="M0,102 C42,44 122,38 202,38 C462,38 705,182 1050,312 L1050,600 L0,600 Z" fill="var(--accent-red)"/>
    <path d="M0,108 C50,52 130,45 210,45 C470,45 720,200 1050,358 L1050,600 L0,600 Z" fill="var(--card-black)"/>
  </svg>

  <div class="holder">
    <p class="holder__name">Marla Kenton</p>
    <p class="holder__title">President</p>
  </div>

  <p class="company-name">Brell Stone Company</p>

  <ul class="contact-list">
    <li>
      <svg viewBox="0 0 24 24" aria-hidden="true"><path fill="var(--accent-red)" d="M6.6 10.8a15.2 15.2 0 0 0 6.6 6.6l2.2-2.2c.3-.3.7-.4 1-.2 1.1.4 2.300.6 3.6.6.6 0 1 .4 1 1V20c0 .6-.4 1-1 1A17 17 0 0 1 3 4c0-.6.4-1 1-1h3.5c.6 0 1 .4 1 1 0 1.3.2 2.5.6 3.6.1.3 0 .7-.2 1z"/></svg>
      <span>(555) 014-2290</span>
    </li>
    <li>
      <svg viewBox="0 0 24 24" aria-hidden="true"><rect x="2" y="5" width="20" height="14" fill="var(--accent-red)"/><path d="M2 5l10 8 10-8M2 19l7.5-7M22 19l-7.5-7" stroke="var(--card-black)" stroke-width="1.6" fill="none"/></svg>
      <span>info@brellstone-example.com</span>
    </li>
    <li>
      <svg viewBox="0 0 24 24" aria-hidden="true"><g fill="none" stroke="var(--accent-red)" stroke-width="1.6"><circle cx="12" cy="12" r="10"/><ellipse cx="12" cy="12" rx="4.5" ry="10"/><path d="M2 12h20M4 6.5h16M4 17.5h16M12 2v20"/></g></svg>
      <span>www.brellstone-example.com</span>
    </li>
  </ul>

  <div class="divider" aria-hidden="true"></div>

  <address class="address">
    48 Harbor Works Lane<br>
    Millbrook, NY 10599
  </address>
</section>

<section class="card card--back" aria-label="Business card back">
  <p class="company-name">Brell Stone Company</p>
  <p class="back-url">www.brellstone-example.com</p>
</section>

</body>
</html>
```